Veldmark Supplies Business Card

Professional business card that stand out to our potential customers. Front and back with clean modern design

Industry/Entity Type

Oil and gas

Contact Information for Business Card

Name, address, website , office phone and cell number

Requirements
Must have
• Editable files for each employee

```html
<!DOCTYPE html>
<html lang="en">
<head>
<meta charset="UTF-8">
<title>Veldmark Supplies Business Card</title>
<link href="https://fonts.googleapis.com/css2?family=Poppins:wght@400;500;600;700&display=swap" rel="stylesheet">
<style>
  :root {
    --red: #ec2327;
    --blue: #12b0d2;
    --ink: #1d1d1f;
    --paper: #ffffff;
    --backdrop: #e2e6e8;
  }
  * { box-sizing: border-box; margin: 0; padding: 0; }
  html, body {
    width: 1200px;
    height: 960px;
    overflow: hidden;
    background: var(--backdrop);
    font-family: "Poppins", sans-serif;
  }
  .card {
    position: absolute;
    left: 250px;
    width: 702px;
    height: 400px;
    background: var(--paper);
    border-radius: 28px;
    border-left: 4px solid var(--red);
    border-bottom: 4px solid var(--red);
  }
  .card--front { top: 60px; }
  .card--back { top: 500px; }

  .brand {
    position: absolute;
    display: flex;
    align-items: center;
    gap: 12px;
    white-space: nowrap;
  }
  .brand__mark {
    width: 18px;
    height: 18px;
    background: var(--blue);
  }
  .brand__name {
    font-weight: 700;
    color: var(--red);
    letter-spacing: 0.5px;
  }
  .card--front .brand {
    left: 50%;
    top: 50%;
    transform: translate(-50%, -50%);
  }
  .card--front .brand__name { font-size: 38px; }
  .card--front .brand__mark { width: 26px; height: 26px; }

  .card--back .brand {
    left: 170px;
    top: 200px;
    transform: translate(-50%, -50%);
  }
  .card--back .brand__name { font-size: 24px; }

  .divider {
    position: absolute;
    left: 346px;
    top: 94px;
    width: 1px;
    height: 214px;
    background: var(--red);
  }
  .contact {
    position: absolute;
    left: 399px;
    top: 116px;
  }
  .contact__name {
    font-size: 33px;
    line-height: 1.1;
    color: var(--blue);
    font-weight: 400;
  }
  .contact__name strong { color: var(--red); font-weight: 600; }
  .contact__role {
    font-size: 17px;
    color: var(--blue);
    margin-top: 3px;
  }
  .contact__list {
    list-style: none;
    margin-top: 16px;
  }
  .contact__list li {
    display: flex;
    align-items: center;
    gap: 11px;
    font-size: 19px;
    color: var(--ink);
    height: 23.5px;
  }
  .contact__list svg { width: 16px; height: 16px; flex: none; }
  .address {
    position: absolute;
    left: 0;
    right: 0;
    top: 356px;
    text-align: center;
    font-size: 17.5px;
    color: var(--red);
  }
</style>
</head>
<body>
  <section class="card card--front">
    <div class="brand">
      <span class="brand__mark"></span>
      <span class="brand__name">Veldmark Supplies</span>
    </div>
  </section>

  <section class="card card--back">
    <div class="brand">
      <span class="brand__mark"></span>
      <span class="brand__name">Veldmark Supplies</span>
    </div>
    <div class="divider"></div>
    <div class="contact">
      <h1 class="contact__name"><strong>Lenka</strong> Dvorakova</h1>
      <p class="contact__role">Co-Founder &amp; CEO</p>
      <ul class="contact__list">
        <li>
          <svg viewBox="0 0 16 16"><path d="M3.5 1.5l2.5 3-1.5 1.5c.8 2 2.5 3.7 4.5 4.5L10.5 9l3 2.5-1.5 2.5C7 14 2 9 2 3z" fill="var(--red)"/></svg>
          (555) 014-3920
        </li>
        <li>
          <svg viewBox="0 0 16 16"><rect x="4" y="1" width="8" height="14" rx="1.5" fill="none" stroke="var(--blue)" stroke-width="1.5"/><circle cx="8" cy="12.5" r="0.9" fill="var(--blue)"/></svg>
          (555) 018-6641
        </li>
        <li>
          <svg viewBox="0 0 16 16"><circle cx="8" cy="8" r="7" fill="var(--red)"/><path d="M1 8h14M8 1c-3 3-3 11 0 14M8 1c3 3 3 11 0 14" fill="none" stroke="#fff" stroke-width="1"/></svg>
          www.website.com
        </li>
        <li>
          <svg viewBox="0 0 16 16"><rect x="1" y="4" width="14" height="10" fill="none" stroke="var(--blue)" stroke-width="1.5"/><path d="M1 4l7 5 7-5" fill="none" stroke="var(--blue)" stroke-width="1.5"/></svg>
          info@website.com
        </li>
      </ul>
    </div>
    <p class="address">1480 Ridgeway Ave. Suite 310 Midland, TX 79701</p>
  </section>
</body>
</html>
```